Clear Plastic Card Design

I am looking to have a business card designed from my logo icon. I am looking to match the style of a different business card I have attached in the files.
Looking for a card that is plastic, with layers of transparency in the shape of my logo icon (also attached in the files) - not a circle like the other card. The winning design will incorporate the red icon logo on the front and back and include the charity's name, "Light for the Weary Souls" in the same or similar font, as well as an email and phone number. For now, use the email: email@lightfortheweary-mail.org and the phone number 555-382-7194.
We like how the sample business card has transparency, partial and full opacity layers and a matching color scheme. Files will need to be in vector so that our business card printing company can work with it.
UPDATE:
We've some excellent designs in, thank you everyone! I got an early review from the owner, and he requested a minor redirect to find his perfect design. He wants the design to stand out by NOT being a rectangle. Try instead a circle, square, or best yet - something that falls in the outline of the logo icon, either fully or partially. Thank you, everyone!
Light for the Weary Souls text should be incorporated as well as a phone and email.

```html
<!DOCTYPE html>
<html lang="en">
<head>
<meta charset="utf-8">
<title>Light for the Weary Souls – Clear Business Card</title>
<link rel="stylesheet" href="https://fonts.googleapis.com/css2?family=Open+Sans:wght@400;600;700&display=swap">
<style>
  :root {
    --page-top: #d8d0c6;
    --page-bottom: #c9bfb3;
    --plastic: rgba(250, 247, 242, 0.62);
    --plastic-edge: rgba(255, 255, 255, 0.85);
    --accent-red: #c9301a;
    --accent-orange: #d6481c;
    --accent-deep: #a3121a;
    --ink: #3a3a3a;
    --ink-dark: #1a1a1a;
  }
  html, body {
    margin: 0;
    padding: 0;
    width: 1200px;
    height: 926px;
    overflow: hidden;
    background: linear-gradient(180deg, var(--page-top) 0%, var(--page-bottom) 100%);
    font-family: "Open Sans", Arial, sans-serif;
  }
  .card-shadow {
    position: absolute;
    left: 50px;
    top: 156px;
    width: 1100px;
    height: 614px;
    filter: drop-shadow(0 8px 22px rgba(0, 0, 0, 0.18));
  }
  .business-card {
    position: relative;
    width: 100%;
    height: 100%;
    overflow: hidden;
    background:
      linear-gradient(125deg, rgba(255,255,255,0.55) 0%, rgba(255,255,255,0.08) 40%, rgba(255,255,255,0.3) 70%, rgba(255,255,255,0.05) 100%),
      var(--plastic);
    clip-path: polygon(70px 0, 100% 0, 100% calc(100% - 70px), calc(100% - 70px) 100%, 0 100%, 0 70px);
  }
  .card-edge {
    position: absolute;
    inset: 0;
    width: 100%;
    height: 100%;
    pointer-events: none;
  }
  .faint-square {
    position: absolute;
    right: 0;
    top: 192px;
    width: 430px;
    height: 391px;
    background: linear-gradient(160deg, rgba(214, 72, 28, 0.10) 0%, rgba(201, 48, 26, 0.22) 100%);
  }
  .org-name {
    position: absolute;
    left: 52px;
    top: 198px;
    margin: 0;
    display: flex;
    align-items: center;
    gap: 14px;
    font-size: 38px;
    font-weight: 400;
    line-height: 1.12;
    color: var(--ink-dark);
  }
  .org-name__square {
    width: 24px;
    height: 24px;
    background: var(--accent-red);
    flex: none;
  }
  .person {
    position: absolute;
    right: 53px;
    top: 72px;
    text-align: right;
  }
  .person__name {
    margin: 0;
    font-size: 43px;
    font-weight: 600;
    letter-spacing: 0.5px;
    color: var(--accent-orange);
    line-height: 1.1;
  }
  .person__title {
    margin: 0;
    font-size: 29px;
    font-weight: 400;
    color: var(--ink);
    line-height: 1.3;
  }
  .accent-bar {
    position: absolute;
    right: 0;
    top: 68px;
    width: 28px;
    height: 91px;
    background: var(--accent-red);
  }
  .contact {
    position: absolute;
    left: 52px;
    top: 452px;
    margin: 0;
    padding: 0;
    list-style: none;
    font-size: 30px;
    color: var(--ink);
    line-height: 38px;
  }
  .contact__item {
    display: flex;
    align-items: center;
    gap: 8px;
  }
  .contact__icon {
    width: 22px;
    height: 22px;
    flex: none;
  }
  .bottom-band {
    position: absolute;
    left: 0;
    bottom: 0;
    width: 100%;
    height: 32px;
    background: linear-gradient(90deg, var(--accent-orange) 0%, var(--accent-deep) 20%, var(--accent-red) 45%, var(--accent-deep) 65%, var(--accent-red) 85%, var(--accent-orange) 100%);
    opacity: 0.92;
  }
</style>
</head>
<body>
  <div class="card-shadow">
    <div class="business-card">
      <div class="faint-square"></div>

      <h1 class="org-name">
        <span class="org-name__square"></span>
        <span>Light for the<br>Weary Souls</span>
      </h1>

      <div class="person">
        <p class="person__name">DANIEL HARTLEY</p>
        <p class="person__title">Managing Director</p>
      </div>
      <div class="accent-bar"></div>

      <ul class="contact">
        <li class="contact__item">
          <svg class="contact__icon" viewBox="0 0 24 24" aria-hidden="true">
            <path fill="#c9301a" d="M2 9c0-3 5-5 10-5s10 2 10 5v2h-5V9c-1-1-3-1.5-5-1.5S8 8 7 9v2H2z"/>
            <path fill="#c9301a" d="M6 12h12l2 8H4z"/>
          </svg>
          <span>555-382-7194</span>
        </li>
        <li class="contact__item">
          <svg class="contact__icon" viewBox="0 0 24 24" aria-hidden="true">
            <path fill="#c9301a" d="M2 10l10-7 10 7v11H2z"/>
            <path fill="none" stroke="#f4f1ec" stroke-width="1.6" d="M2.5 10.5l9.5 6.5 9.5-6.5M3 20.5l7-5.5M21 20.5l-7-5.5"/>
          </svg>
          <span>email@lightfortheweary-mail.org</span>
        </li>
      </ul>

      <div class="bottom-band"></div>

      <svg class="card-edge" viewBox="0 0 1100 614" preserveAspectRatio="none" aria-hidden="true">
        <polygon points="70,1 1099,1 1099,544 1030,613 1,613 1,70" fill="none" stroke="rgba(255,255,255,0.85)" stroke-width="2"/>
      </svg>
    </div>
  </div>
</body>
</html>
```